Brindlemark Group information card

We need a 5x7 two-sided card to hand out at open houses and provide to our charitable partners for distribution. We are a local real estate group looking to add a "give back" component to our business. We are located in a coastal community and would like to incorporate that feel into our design. We are giving clients who use us the ability to designate 1 out of the 10 charitable organizations we partner with - and we will make a donation to that organization.

We included the 10 partner logos below - we envision them pretty small. Also included 2 photos of the "Brindlemark" and our logo. Have fun.
Updates

Target Market(s)

home buyers & sellers

Industry/Entity Type

Real Estate

Font styles to use
Serif
Sans Serif

Colors

Designer to choose colors to be used in the design.

Requirements
Must have
• slogan & tagline - see attached text file
• Brindlemark photo
Nice to have
• partner logos - small - maybe in circles?

```html
<!DOCTYPE html>
<html lang="en">
<head>
<meta charset="utf-8">
<title>Brindlemark Group – Change Homes, Change Lives</title>
<link href="https://fonts.googleapis.com/css2?family=Josefin+Sans:wght@400;600&family=Source+Sans+3:wght@400;600&family=Quicksand:wght@500&family=Arimo:wght@400&display=swap" rel="stylesheet">
<style>
  :root {
    --sky-top: #6f7fb4;
    --sky-pink: #e98a82;
    --sky-glow: #f2a27c;
    --sea: #d98680;
    --city: #3a3446;
    --city-deep: #1f1c26;
    --band-blue: #5b88c8;
    --panel-dark: rgba(40, 52, 78, 0.72);
    --white: #ffffff;
    --ink: #1a1a1a;
    --link-blue: #4f7fc0;
  }
  * { margin: 0; padding: 0; box-sizing: border-box; }
  html, body { width: 857px; height: 1200px; overflow: hidden; background: var(--white); }
  .card { position: relative; width: 857px; height: 1200px; background: var(--white); overflow: hidden; }

  .hero-photo {
    position: absolute; left: 0; top: 0; width: 857px; height: 890px;
    background: linear-gradient(180deg,
      var(--sky-top) 0%,
      var(--sky-pink) 14%,
      var(--sky-glow) 28%,
      #e07f77 38%,
      var(--sea) 40%,
      #c77a78 48%,
      #6a5560 55%,
      var(--city) 68%,
      var(--city-deep) 100%);
  }

  .brand-name {
    position: absolute; right: 44px; top: 118px; width: 330px;
    text-align: center; color: var(--white);
    font-family: "Source Sans 3", sans-serif; font-weight: 600;
    line-height: 1.02;
  }
  .brand-name .brand-main { display: block; font-size: 54px; letter-spacing: 0.5px; }
  .brand-name .brand-sub { display: block; font-size: 44px; margin-top: 6px; }

  .slogan-band {
    position: absolute; left: 0; top: 718px; width: 527px; height: 172px;
    background: var(--band-blue);
    box-shadow: 4px 4px 10px rgba(0,0,0,0.35);
    display: flex; align-items: center; padding-left: 36px;
  }
  .slogan {
    color: var(--white); font-family: "Josefin Sans", sans-serif; font-weight: 400;
    font-size: 52px; line-height: 58px; letter-spacing: 1px; padding-top: 8px;
  }

  .tagline-panel {
    position: absolute; left: 527px; top: 718px; width: 330px; height: 172px;
    background: var(--panel-dark);
    display: flex; align-items: center; justify-content: center;
  }
  .tagline {
    color: var(--white); font-family: "Quicksand", sans-serif; font-weight: 500;
    font-size: 24px; line-height: 34px; text-align: center;
  }

  .pledge {
    position: absolute; left: 50px; top: 926px; width: 757px;
    font-family: "Arimo", sans-serif; font-size: 19.5px; line-height: 31px;
    color: var(--ink); text-align: justify; text-align-last: center;
  }

  .web-icon { position: absolute; left: 406px; top: 1087px; width: 52px; height: 52px; }
  .web-address {
    position: absolute; left: 0; top: 1148px; width: 857px; text-align: center;
    font-family: "Arimo", sans-serif; font-size: 17px; color: var(--link-blue);
  }
</style>
</head>
<body>
<main class="card">
  <div class="hero-photo" role="img" aria-label="Coastal town at sunset seen from a hillside, pink sky over a curved bay with a pier and city lights"></div>

  <div class="brand-name">
    <span class="brand-main">Brindlemark</span>
    <span class="brand-sub">Group</span>
  </div>

  <div class="slogan-band">
    <h1 class="slogan">CHANGE HOMES,<br>CHANGE LIVES</h1>
  </div>

  <div class="tagline-panel">
    <p class="tagline">Changing the World<br>One Home at a Time</p>
  </div>

  <p class="pledge">Because we value generosity and desire to make a difference in our community and world, for every home bought or sold through us, we will make a contribution to one of our amazing partner who are helping to change the world.</p>

  <svg class="web-icon" viewBox="0 0 52 52" aria-hidden="true">
    <circle cx="26" cy="26" r="26" fill="var(--band-blue)"/>
    <text x="26" y="28" text-anchor="middle" font-family="Arimo, sans-serif" font-size="12" fill="#fff">www</text>
    <path d="M31 31 L31 41 L33.5 38.5 L35.5 42.5 L37 41.8 L35 37.8 L38.5 37.8 Z" fill="#fff"/>
  </svg>
  <p class="web-address">www.brindlemarkgroup.com</p>
</main>
</body>
</html>
```